The most modern business card ever !!!

Our company call “Vendalo”. Vendalo is a technology company specialized in cruises solutions. Out main product is a platform to reserve cruises. This is a revolutionary platform that make easier to travel agencies and final users to reserve cruises across dozen companies like tibba, wernu, hpv, dgb, etc..We are a “start up”, with a young team of developers and we want to transmit it.. For it, we want something different, a modern business card that represent cruises and technology.. When someone receive this card, this person should say: wowww this is different… this is modern… this is a cruise related company..
- diferent, modern
- traditions business card

```html
<!DOCTYPE html>
<html lang="en">
<head>
<meta charset="utf-8">
<title>Vendalo – Business Card</title>
<link href="https://fonts.googleapis.com/css2?family=Work+Sans:wght@400;500;600&display=swap" rel="stylesheet">
<style>
  :root {
    --backdrop: #161616;
    --card: #242424;
    --card-edge: #2e2e2e;
    --ink: #ffffff;
    --ink-soft: #e6e6e6;
    --accent: #29a8e0;
  }
  * { margin: 0; padding: 0; box-sizing: border-box; }
  html, body {
    width: 1200px; height: 900px; overflow: hidden;
    background: var(--backdrop);
    font-family: "Work Sans", sans-serif;
  }
  .canvas {
    position: relative; width: 1200px; height: 900px;
  }
  .card {
    position: absolute; left: 250px; width: 700px; height: 400px;
    background: linear-gradient(135deg, var(--card) 0%, var(--card-edge) 70%, var(--card) 100%);
    box-shadow: 0 12px 30px rgba(0,0,0,0.55);
  }
  .card--front { top: 40px; display: flex; align-items: center; justify-content: center; }
  .card--back { top: 460px; }

  .wordmark {
    color: var(--ink);
    font-weight: 600;
    letter-spacing: 0.04em;
  }
  .card--front .wordmark { font-size: 104px; }

  .card--back .wordmark {
    position: absolute; left: 50px; top: 148px;
    font-size: 74px;
  }
  .divider {
    position: absolute; left: 382px; top: 100px;
    width: 2px; height: 205px; background: var(--accent);
  }
  .contact {
    position: absolute; left: 412px; top: 96px; width: 270px;
    color: var(--ink-soft);
  }
  .contact__name {
    color: var(--accent); font-size: 25px; font-weight: 500;
    letter-spacing: 0.08em; text-transform: uppercase; white-space: nowrap;
  }
  .contact__role {
    font-size: 17px; letter-spacing: 0.1em; margin-top: 2px;
  }
  .contact__address {
    font-size: 17px; letter-spacing: 0.1em; line-height: 1.5; margin-top: 20px;
    font-style: normal;
  }
  .contact__list { list-style: none; margin-top: 12px; }
  .contact__item {
    display: flex; align-items: center; gap: 8px;
    font-size: 17px; letter-spacing: 0.1em; line-height: 1.6; white-space: nowrap;
  }
  .contact__icon { width: 12px; height: 12px; flex: none; }
</style>
</head>
<body>
<main class="canvas">
  <section class="card card--front" aria-label="Card front">
    <span class="wordmark">Vendalo</span>
  </section>

  <section class="card card--back" aria-label="Card back">
    <span class="wordmark">Vendalo</span>
    <div class="divider"></div>
    <div class="contact">
      <p class="contact__name">Daniel Hart</p>
      <p class="contact__role">Director</p>
      <address class="contact__address">48 Harbour Lane,<br>Wellport, NZ, 6021</address>
      <ul class="contact__list">
        <li class="contact__item">
          <svg class="contact__icon" viewBox="0 0 12 12" aria-hidden="true">
            <path d="M3 1 L5 3.5 L4 5 Q5 7.2 7 8 L8.5 7 L11 9 L9.5 11 Q4.5 10.5 1 3 Z" fill="none" stroke="#29a8e0" stroke-width="1.2" stroke-linejoin="round"/>
          </svg>
          (555) 012-4789
        </li>
        <li class="contact__item">
          <svg class="contact__icon" viewBox="0 0 12 12" aria-hidden="true">
            <rect x="1" y="2.5" width="10" height="7" fill="none" stroke="#29a8e0" stroke-width="1.2"/>
            <path d="M1 2.5 L6 6.5 L11 2.5" fill="none" stroke="#29a8e0" stroke-width="1.2"/>
          </svg>
          info@vendalo.com.br
        </li>
        <li class="contact__item">
          <svg class="contact__icon" viewBox="0 0 12 12" aria-hidden="true">
            <circle cx="6" cy="6" r="5" fill="none" stroke="#29a8e0" stroke-width="1.1"/>
            <ellipse cx="6" cy="6" rx="2.2" ry="5" fill="none" stroke="#29a8e0" stroke-width="1"/>
            <path d="M1 6 H11 M2 3.5 H10 M2 8.5 H10" stroke="#29a8e0" stroke-width="0.9"/>
          </svg>
          www.vendalo.com.br
        </li>
      </ul>
    </div>
  </section>
</main>
</body>
</html>
```